Brevard Trade Partners - we are Asian sourcing agents

We are sourcing agents based in the USA and we act as sourcing agents for clients in throughout the world. We focus primarily on custom sewn goods. So basically companies who do not have the in-house expertise to do it themselves, come to us and have us find suitable factories in Asia to do the production. We are middlemen. We find the factories...quote the project...manage the quality control and then deliver the goods directly to our customer's door. We pride ourselves in making the communication very easy and precise.

Current page is www.brevardtradepartners.com

I am not happy w/ the overall look. The spacing...the photos, the fonts...the design elements...the pictures. I want a cool, crisp design that conveys professionalism and clearly depicts/explains what we do.

Requirements
Must have
• use my logo....I like it...it was designed by someone on this website.
Nice to have
• a video/animation of the entire process would be wonderful. Showing initial contact with our office in the USA...then to my correspondence with my offices in Taiwan and in Hong Kong...and then back and fort w/ the customer.....and then between my people in Hong Kong/Taiwan with the local factories......and then a quote is generated and sent to my client......to samples being made and sent for approval.....to a PO being generated......to final samples being sent.....to the order being shipped and delivered to the clients warehouse. I was thinking of an animation showing arrows and text showing the back and forth communication and explaining how the process flows.

```html
<!DOCTYPE html>
<html lang="en">
<head>
<meta charset="utf-8">
<title>Brevard Trade Partners – Asian Sourcing Agents</title>
<link href="https://fonts.googleapis.com/css2?family=Lato:wght@400;700;900&family=Montserrat:wght@400;500&display=swap" rel="stylesheet">
<style>
:root{
  --navy:#132b6e;
  --green:#5a9a17;
  --green-dark:#3f7a0c;
  --text:#444;
  --muted:#888;
  --rule:#9a9a9a;
  --footer:#2d2d2d;
  --footer-bar:#4a4a4a;
  --footer-text:#c8c8c8;
  --white:#fff;
}
*{margin:0;padding:0;box-sizing:border-box}
html,body{width:854px;height:1200px;overflow:hidden;background:var(--white)}
body{position:relative;font-family:'Lato',sans-serif;color:var(--text)}
.abs{position:absolute}
.top-rule{left:0;top:0;width:854px;height:2px;background:var(--green)}

/* header */
.brand{left:78px;top:36px;font-family:'Montserrat',sans-serif;font-weight:500;color:var(--navy);font-size:19px;line-height:20px;display:flex;align-items:center;gap:8px}
.brand-square{width:14px;height:14px;background:var(--green)}
.phone{left:472px;top:28px;display:flex;align-items:center;gap:8px;color:var(--green);font-size:16px}
.btn-quote-top{left:620px;top:22px;width:157px;height:32px;background:var(--navy);color:var(--white);font-size:15px;font-weight:700;display:flex;align-items:center;justify-content:center;letter-spacing:.2px}
.main-nav{right:77px;top:68px;display:flex;font-size:12.6px;color:#555}
.main-nav a{color:inherit;text-decoration:none;padding:0 11px;border-left:1px solid #bbb;line-height:17px}
.main-nav a:first-child{border-left:0}
.main-nav a:last-child{padding-right:0}

/* hero */
.hero-frame{left:78px;top:102px;width:698px;height:348px;border:1px solid #ddd}
.hero-photo{left:81px;top:105px;width:692px;height:345px;background:linear-gradient(100deg,#6b6f6a 0%,#b46a7c 25%,#3f4a5c 50%,#6d7a86 75%,#8c979e 100%)}
.hero-title{left:464px;top:186px;color:var(--white);font-weight:700;font-size:22.5px;letter-spacing:-.2px}
.hero-sub{left:464px;top:219px;width:300px;color:var(--white);font-size:16px;line-height:19px;letter-spacing:.3px}
.btn-read{left:465px;top:269px;width:92px;height:28px;background:linear-gradient(#6fae21,var(--green-dark));color:var(--white);border-radius:3px;font-size:12.5px;font-weight:700;display:flex;align-items:center;justify-content:center}

/* categories */
.cat-band{left:78px;top:450px;width:698px;height:141px;background:var(--navy)}
.cat-pointer{left:161px;top:464px;width:0;height:0;border-left:7px solid transparent;border-right:7px solid transparent;border-bottom:9px solid var(--white)}
.cat-thumb{top:475px;width:146px;height:76px;border:2px solid var(--white)}
.cat-label{top:562px;width:146px;text-align:center;color:var(--white);font-size:15px}
.cat-arrow{top:509px;width:22px;height:23px;border-radius:50%;background:#6b6b6b;color:var(--white);font-size:13px;display:flex;align-items:center;justify-content:center}

/* intro columns */
.col-head{top:615px;font-size:16.5px;font-weight:700;color:#555}
.col-rule{top:641px;width:196px;height:1px;background:var(--rule)}
.col-rule::before{content:"";position:absolute;left:0;top:-1px;width:40px;height:2px;background:var(--green)}
.col-text{font-size:9.8px;line-height:16.2px;color:#333}
.col-link{font-size:10.5px;font-weight:700;color:var(--green)}
.video-box{left:333px;top:658px;width:195px;height:107px;border:2px solid var(--navy);background:linear-gradient(160deg,#9fb0c4,#4e6076)}
.btn-quote{left:562px;top:693px;width:190px;height:32px;background:var(--navy);border:2px solid #c4c9d6;border-radius:6px;color:var(--white);font-size:14px;font-weight:700;display:flex;align-items:center;justify-content:center}

/* footer */
.footer{left:0;top:792px;width:854px;height:370px;background:var(--footer)}
.footer-bar{left:0;top:1162px;width:854px;height:38px;background:var(--footer-bar);color:var(--white);font-family:'Montserrat',sans-serif;font-size:9.6px;display:flex;align-items:center;justify-content:center}
.f-head{font-family:'Montserrat',sans-serif;font-weight:500;font-size:14.6px;line-height:18px;color:var(--white)}
.f-list{list-style:none;font-size:10.2px;color:var(--footer-text)}
.f-list li{height:17.8px;line-height:17.8px;padding-left:9px;position:relative}
.f-list li::before{content:"›";position:absolute;left:0;top:-1px;color:var(--footer-text)}
.f-addr{font-size:10.2px;line-height:15px;color:var(--footer-text)}
.f-brand{left:78px;top:1048px;font-family:'Montserrat',sans-serif;font-weight:500;color:var(--green);font-size:16px;line-height:18px}
.follow{left:78px;top:1103px;display:flex;align-items:center;gap:6px;color:var(--white);font-size:10px}
.social{width:24px;height:24px;border:1.5px solid var(--white);border-radius:50%}
</style>
</head>
<body>
<div class="abs top-rule"></div>

<header>
  <div class="abs brand"><span class="brand-square"></span>Brevard Trade Partners</div>
  <div class="abs phone">
    <svg width="10" height="18" viewBox="0 0 10 18" aria-hidden="true"><path d="M7 1 C2 2 1 5 1 9 C1 13 2 16 7 17 L8 13 L5 12 C4 10 4 8 5 6 L8 5 Z" fill="#555"/></svg>
    <span>1800 555 0142</span>
  </div>
  <div class="abs btn-quote-top">REQUEST A QUOTE</div>
  <nav class="abs main-nav">
    <a href="#">Home</a><a href="#">Product Categories</a><a href="#">About Us</a><a href="#">Request Quote</a><a href="#">Contact Us</a>
  </nav>
</header>

<section class="hero">
  <div class="abs hero-frame"></div>
  <div class="abs hero-photo" role="img" aria-label="Two garment workers inspecting fabric on a cutting table in a factory"></div>
  <div class="abs hero-title">Asian Outsourcing Made Easy!</div>
  <div class="abs hero-sub">Custom Sewn Goods Made to Your Specifications</div>
  <div class="abs btn-read">Read More</div>
</section>

<section class="categories">
  <div class="abs cat-band"></div>
  <div class="abs cat-pointer"></div>
  <div class="abs cat-thumb" style="left:96px;background:linear-gradient(100deg,#8a7a78,#b54a6a,#5f6b76)" role="img" aria-label="Workers at a sewing factory table"></div>
  <div class="abs cat-thumb" style="left:266px;background:linear-gradient(160deg,#6f7884,#2f3440,#c9b99a)" role="img" aria-label="Open black bag filled with books"></div>
  <div class="abs cat-thumb" style="left:437px;background:linear-gradient(170deg,#8e8a80,#2d2f52,#9a9589)" role="img" aria-label="Motorcycle under a fitted cover"></div>
  <div class="abs cat-thumb" style="left:608px;background:linear-gradient(170deg,#cfe0a8,#7fb03a,#5f9a25)" role="img" aria-label="Gloved hand with a golf club and ball on grass"></div>
  <div class="abs cat-label" style="left:96px">Sewn Goods</div>
  <div class="abs cat-label" style="left:266px;top:559px">Bags</div>
  <div class="abs cat-label" style="left:437px">Covers</div>
  <div class="abs cat-label" style="left:608px">Gloves</div>
  <div class="abs cat-arrow" style="left:63px">‹</div>
  <div class="abs cat-arrow" style="left:771px">›</div>
</section>

<section class="intro">
  <h2 class="abs col-head" style="left:93px">Welcome to Brevard</h2>
  <div class="abs col-rule" style="left:93px"></div>
  <p class="abs col-text" style="left:96px;top:650px;width:210px">Lorem Ipsum is simply dummy text of the printing and typesetting industry. Lorem Ipsum has been the industry's standard dummy text ever since the 1500s, when an unknown printer took a galley of type and scrambled it to make a type specimen with book ending.</p>
  <div class="abs col-link" style="left:96px;top:753px">Read More &nbsp; &gt;&gt;</div>

  <h2 class="abs col-head" style="left:333px">Our Video</h2>
  <div class="abs col-rule" style="left:333px"></div>
  <div class="abs video-box" role="img" aria-label="Video still of a sewing machine needle"></div>
  <svg class="abs" style="left:416px;top:698px" width="28" height="28" viewBox="0 0 28 28" aria-hidden="true"><circle cx="14" cy="14" r="12" fill="none" stroke="#fff" stroke-width="2"/><path d="M11 8 L20 14 L11 20 Z" fill="#fff"/></svg>

  <h2 class="abs col-head" style="left:562px">From the Quote</h2>
  <div class="abs col-rule" style="left:563px"></div>
  <p class="abs col-text" style="left:563px;top:650px;width:205px">Please contact us for immediate consultation regarding your outsourcing project.</p>
  <div class="abs btn-quote">REQUEST A QUOTE</div>
  <div class="abs col-link" style="left:563px;top:738px">View More Quote &nbsp; &gt;&gt;</div>
</section>

<footer>
  <div class="abs footer"></div>

  <h3 class="abs f-head" style="left:78px;top:817px">Us Headquarters</h3>
  <p class="abs f-addr" style="left:78px;top:849px">Brevard Trade Partners<br>48 Harbor Lane<br>Suite 3B<br>Portsmouth, NH 03801</p>
  <h3 class="abs f-head" style="left:78px;top:935px">Online: Inquiry Form</h3>
  <ul class="abs f-list" style="left:78px;top:972px">
    <li>Tel: 603-555-0187</li><li>Fax: 603-555-0193</li><li>Mail: info@brevardtrade.com</li>
  </ul>
  <div class="abs f-brand">Brevard Trade Partners</div>
  <div class="abs follow">Follow Us: &nbsp;<span class="social"></span><span class="social"></span><span class="social"></span></div>

  <h3 class="abs f-head" style="left:286px;top:817px">Custom Bags</h3>
  <ul class="abs f-list" style="left:286px;top:846px">
    <li>Athletic Bags</li><li>Backpacks</li><li>Computer Bags</li><li>Cooler Bags</li><li>Cosmetic Bags</li><li>Handbags</li><li>Messenger Bags</li><li>Shopping Bags</li><li>Tool Bags</li><li>Travel Bags</li><li>Yoga Bags</li>
  </ul>
  <h3 class="abs f-head" style="left:286px;top:1057px">Custom Sporting<br>Goods</h3>
  <ul class="abs f-list" style="left:286px;top:1101px">
    <li>Yoga Mats</li><li>Yoga Gear and Accessories</li>
  </ul>

  <h3 class="abs f-head" style="left:453px;top:817px">Custom Covers</h3>
  <ul class="abs f-list" style="left:453px;top:846px">
    <li>ATV Covers</li><li>Chair Covers</li><li>Equipment Covers</li><li>Golf Cart Covers</li><li>Motorcycle Covers</li><li>Outdoor Furniture Covers</li><li>Outdoor Grill Cover</li><li>Personal Watercraft Covers</li><li>Snowmobile Covers</li>
  </ul>
  <h3 class="abs f-head" style="left:453px;top:1017px">Custom Medical<br>Accessories</h3>
  <ul class="abs f-list" style="left:453px;top:1061px">
    <li>Medical Equipment Covers</li><li>Medical Pads</li><li>Medical Sheets &amp; Bedding</li><li>Oxygen Tank Cases and Bags</li>
  </ul>

  <h3 class="abs f-head" style="left:652px;top:817px">Custom Gloves</h3>
  <ul class="abs f-list" style="left:652px;top:846px">
    <li>Batting Gloves</li><li>Garden Gloves</li><li>Mechanic Gloves</li><li>Safety Gloves</li><li>Ski Gloves</li>
  </ul>
  <h3 class="abs f-head" style="left:652px;top:944px">Custom Sewn<br>Goods</h3>
  <ul class="abs f-list" style="left:652px;top:987px">
    <li>Pet Collars, Leashes</li><li>Socks</li>
  </ul>
  <h3 class="abs f-head" style="left:652px;top:1034px">Custom Cases</h3>
  <ul class="abs f-list" style="left:652px;top:1061px">
    <li>Cosmetic Cases</li><li>Phone Cases</li><li>Tool Bags and Tool</li><li>Cases</li>
  </ul>

  <div class="abs footer-bar">© Brevard Trade Partners, LLC. I USA - Hong Kong - Taipei</div>
</footer>
</body>
</html>
```